Commercial Refrigeration Service Company requires stylish and fresh looking flyer.

We need a flyer to hand out to new customers. It should have a photo and our branding, list all the services that are offered and our contact details.
We would like two flyers to be supplied, both identical though one offering a discount until July ( Half Price Service Fee ). The flyer should be clear, interesting and in similar colours to the branding package supplied.
Please look at our website for information about the services on offer:
www.brisko-coolworks.com.au

Target Market(s)

Cafes, bars, restaurants, pubs ect.

Font styles to use
Other font styles liked:
• Font package provided

Colors
85cae6
ffffff
333333

Requirements
Must have
• - The photo provided.
• - The company logo.
• - Similar feel to the website & business card.
• - Smooth layout and clear to understand.
Should not have
• - No clunky badges or prints.

```html
<!DOCTYPE html>
<html lang="en">
<head>
<meta charset="utf-8">
<title>Brisko Commercial Refrigeration Flyer</title>
<link rel="stylesheet" href="https://fonts.googleapis.com/css2?family=Questrial&family=Oswald:wght@400&family=Titillium+Web:wght@600&display=swap">
<style>
  :root {
    --brand-blue: #5bc4ef;
    --accent-blue: #4fb3e0;
    --ink: #222222;
    --dark-band: #2a2e30;
    --icon-grey: #8b8e91;
    --paper-top: #f6f6f6;
    --paper-bottom: #e6e6e6;
    --backdrop: #1f1e1f;
  }
  * { box-sizing: border-box; margin: 0; padding: 0; }
  html, body {
    width: 1200px; height: 1146px; overflow: hidden;
    background: var(--backdrop);
  }
  .flyer {
    position: absolute; left: 200px; top: 7px;
    width: 800px; height: 1131px;
    background: linear-gradient(var(--paper-top), var(--paper-bottom));
    overflow: hidden;
  }
  .header-band {
    position: absolute; left: 0; top: 0; width: 800px; height: 134px;
    background: var(--brand-blue);
  }
  .brand {
    position: absolute; left: 60px; top: 48px; width: 240px;
    display: flex; align-items: center; justify-content: center; gap: 10px;
  }
  .brand-dot {
    width: 14px; height: 14px; border-radius: 50%; background: var(--ink);
  }
  .brand-name {
    font-family: "Questrial", sans-serif; font-size: 32px; line-height: 38px;
    color: var(--ink);
  }
  .social-row {
    position: absolute; right: 51px; top: 23px; display: flex; gap: 3px;
  }
  .social-row span {
    width: 21px; height: 21px; border-radius: 50%; background: #111;
  }
  .contact-block {
    position: absolute; right: 51px; top: 52px; text-align: right;
    font-family: "Questrial", sans-serif; font-size: 17px; line-height: 21px;
    color: #111;
  }
  .hero-photo {
    position: absolute; left: 0; top: 134px; width: 800px; height: 405px;
    background: linear-gradient(180deg, #c9d6e0 0%, #b9c6cf 30%, #7e8488 55%, #6a6c6e 100%);
  }
  .section-title {
    position: absolute; left: 0; top: 580px; width: 800px; text-align: center;
    font-family: "Titillium Web", sans-serif; font-weight: 600;
    font-size: 21px; color: var(--accent-blue); letter-spacing: 0.5px;
  }
  .section-title .diamonds {
    font-size: 9px; letter-spacing: 16px; vertical-align: middle; margin: 0 8px;
  }
  .service {
    position: absolute; width: 200px; margin-left: -100px; text-align: center;
  }
  .service svg { display: block; margin: 0 auto; }
  .service-label {
    display: block; margin-top: 14px;
    font-family: "Oswald", sans-serif; font-size: 20px;
    color: var(--accent-blue); transform: scaleX(0.82); white-space: nowrap;
  }
  .offer-box {
    position: absolute; left: 133px; top: 919px; width: 534px; height: 120px;
    border: 1.5px dotted #555; text-align: center;
  }
  .offer-headline {
    margin-top: 15px;
    font-family: "Questrial", sans-serif; font-size: 49px; line-height: 52px;
    color: var(--accent-blue); letter-spacing: -0.5px;
  }
  .offer-detail {
    font-family: "Questrial", sans-serif; font-size: 24px;
    color: var(--accent-blue);
  }
  .cut-mark { position: absolute; }
  .footer-band {
    position: absolute; left: 0; top: 1077px; width: 800px; height: 54px;
    background: var(--dark-band); text-align: center;
    font-family: "Titillium Web", sans-serif; font-weight: 600;
    font-size: 25px; line-height: 54px; color: var(--brand-blue);
    letter-spacing: 0.5px;
  }
</style>
</head>
<body>
<div class="flyer">
  <div class="header-band">
    <div class="brand"><span class="brand-dot"></span><span class="brand-name">Brisko</span></div>
    <div class="social-row"><span></span><span></span><span></span></div>
    <div class="contact-block">
      PO Box 1180 Harbourview NSW 2099<br>
      0400 123 456 &nbsp;|&nbsp; info@brisko-coolworks.com.au<br>
      ABN: 12 345 678 901 &nbsp;|&nbsp; Licence No: 401122B
    </div>
  </div>

  <div class="hero-photo" role="img" aria-label="Technician leaning on a grey branded service ute parked by the beach"></div>

  <h2 class="section-title"><span class="diamonds">◇◇◇</span>OUR SERVICES<span class="diamonds">◇◇◇</span></h2>

  <div class="service" style="left:200px; top:641px;">
    <svg width="68" height="68" viewBox="0 0 68 68"><circle cx="34" cy="34" r="32" fill="var(--icon-grey)" stroke="var(--accent-blue)" stroke-width="2"/><g fill="none" stroke="#fff" stroke-width="2"><rect x="29" y="14" width="8" height="28" rx="4"/><circle cx="33" cy="47" r="7"/><path d="M41 18h6M41 23h4M41 28h6M41 33h4"/></g></svg>
    <span class="service-label">COMMERCIAL REFRIGERATION</span>
  </div>
  <div class="service" style="left:380px; top:641px;">
    <svg width="68" height="68" viewBox="0 0 68 68"><circle cx="34" cy="34" r="32" fill="var(--icon-grey)" stroke="var(--accent-blue)" stroke-width="2"/><g fill="none" stroke="#fff" stroke-width="2"><path d="M21 15h26l-3 38H24z"/><rect x="27" y="26" width="8" height="8"/><rect x="34" y="33" width="8" height="8"/><rect x="27" y="39" width="7" height="7"/></g></svg>
    <span class="service-label">ICE MAKERS</span>
  </div>
  <div class="service" style="left:525px; top:641px;">
    <svg width="68" height="68" viewBox="0 0 68 68"><circle cx="34" cy="34" r="32" fill="var(--icon-grey)" stroke="var(--accent-blue)" stroke-width="2"/><g fill="none" stroke="#fff" stroke-width="2"><path d="M38 14l4 2-6 16"/><path d="M24 32h16v10h-6v4h-4v-4h-6z"/><path d="M36 46v6"/><circle cx="36" cy="54" r="2"/></g></svg>
    <span class="service-label">BEER SYSTEMS</span>
  </div>
  <div class="service" style="left:658px; top:641px;">
    <svg width="68" height="68" viewBox="0 0 68 68"><circle cx="34" cy="34" r="32" fill="var(--icon-grey)" stroke="var(--accent-blue)" stroke-width="2"/><path d="M38 13L25 36h9l-4 19 13-25h-9z" fill="none" stroke="#fff" stroke-width="2" stroke-linejoin="round"/></svg>
    <span class="service-label">ELECTRICAL</span>
  </div>

  <div class="service" style="left:261px; top:769px;">
    <svg width="68" height="68" viewBox="0 0 68 68"><circle cx="34" cy="34" r="32" fill="var(--icon-grey)" stroke="var(--accent-blue)" stroke-width="2"/><g fill="none" stroke="#fff" stroke-width="2"><path d="M20 20l28 28M18 24a6 6 0 0 0 8-8"/><path d="M48 18L22 46M44 16l8 4-4 4z"/></g></svg>
    <span class="service-label">24HR SERVICE</span>
  </div>
  <div class="service" style="left:395px; top:769px;">
    <svg width="68" height="68" viewBox="0 0 68 68"><circle cx="34" cy="34" r="32" fill="var(--icon-grey)" stroke="var(--accent-blue)" stroke-width="2"/><g fill="none" stroke="#fff" stroke-width="2"><path d="M14 22h6l4 18h24l4-14H22"/><circle cx="28" cy="46" r="3"/><circle cx="44" cy="46" r="3"/></g></svg>
    <span class="service-label">SALES</span>
  </div>
  <div class="service" style="left:531px; top:769px;">
    <svg width="68" height="68" viewBox="0 0 68 68"><circle cx="34" cy="34" r="32" fill="var(--icon-grey)" stroke="var(--accent-blue)" stroke-width="2"/><g fill="none" stroke="#fff" stroke-width="2"><path d="M18 42l24-24 6 6-24 24h-6z"/><path d="M20 20l28 28-4 4-28-28z"/></g></svg>
    <span class="service-label">INSTALLATION</span>
  </div>

  <div class="offer-box">
    <div class="offer-headline">DISCOUNT UNTIL JULY</div>
    <div class="offer-detail">PAY ONLY HALF PRICE OF THE SERVICE FEE</div>
    <svg class="cut-mark" style="left:28px; top:-6px;" width="24" height="12" viewBox="0 0 24 12"><g fill="none" stroke="#444" stroke-width="1.3"><circle cx="4" cy="3" r="2.5"/><circle cx="4" cy="9" r="2.5"/><path d="M6 4l16 4M6 8l16-4"/></g></svg>
    <svg class="cut-mark" style="right:30px; bottom:-6px;" width="24" height="12" viewBox="0 0 24 12"><g fill="none" stroke="#444" stroke-width="1.3"><circle cx="20" cy="3" r="2.5"/><circle cx="20" cy="9" r="2.5"/><path d="M18 4L2 8M18 8L2 4"/></g></svg>
  </div>

  <div class="footer-band">WWW.BRISKO-COOLWORKS.COM.AU</div>
</div>
</body>
</html>
```